Pine Hollow Haven Home Inc. Website Update

We have a couple of broken links such as the "contact us" and would like to add board members and a calendar of events. We are open to a new design.

```html
<!DOCTYPE html>
<html lang="en">
<head>
<meta charset="utf-8">
<title>Pine Hollow Haven Home Inc.</title>
<link rel="stylesheet" href="https://fonts.googleapis.com/css2?family=Cinzel:wght@400;700&family=Lato:wght@300;400;700&display=swap">
<style>
:root{
  --taupe:#9b8b7d;
  --taupe-dark:#85715f;
  --brown:#4b3f36;
  --brown-deep:#3a302a;
  --blue:#a9c0ce;
  --blue-dark:#93aabb;
  --pink:#d8608a;
  --ink:#3b3b3b;
  --grey:#6d6d6d;
  --line:#dcdcdc;
  --white:#ffffff;
  --cream:#efe9e3;
}
*{box-sizing:border-box;margin:0;padding:0}
html,body{width:1200px;height:4839px;overflow:hidden}
body{position:relative;background:var(--white);font-family:"Lato",sans-serif;color:var(--ink)}
.abs{position:absolute}
.center{text-align:center}

/* header */
.site-header{top:0;left:0;width:1200px;height:113px;background:var(--white);z-index:3}
.nav{top:50px;display:flex;gap:20px;font-size:13px;font-weight:700;letter-spacing:.3px;color:var(--brown)}
.nav-left{left:165px}
.nav-right{left:690px}
.brand{left:512px;top:0;width:176px;height:160px;border-radius:0 0 88px 88px;background:var(--white);z-index:4;display:flex;align-items:center;justify-content:center;padding:20px 22px 10px}
.brand-name{font-family:"Lato",sans-serif;font-weight:700;font-size:18px;line-height:1.2;color:var(--pink);text-align:center}

/* hero */
.hero{top:113px;left:0;width:1200px;height:670px;background:linear-gradient(160deg,#c9c2ba 0%,#8c7f73 40%,#6e6258 70%,#b3aaa0 100%)}
.hero-arrow{top:250px;width:44px;height:44px;border-radius:50%;background:rgba(255,255,255,.55);display:flex;align-items:center;justify-content:center}
.hero-title{top:150px;left:150px;width:900px;color:var(--white);text-align:center}
.hero-title .pre{font-family:"Cinzel",serif;font-size:46px;letter-spacing:2px}
.hero-title .main{font-family:"Cinzel",serif;font-weight:700;font-size:40px;letter-spacing:.5px;margin-top:6px;white-space:nowrap}
.hero-buttons{top:303px;left:0;width:1200px;display:flex;justify-content:center;gap:20px}
.btn{display:inline-flex;align-items:center;justify-content:center;border-radius:24px;font-size:15px;font-weight:700;letter-spacing:.5px}
.btn-outline{width:176px;height:48px;border:2px solid var(--white);color:var(--white)}
.btn-blue{width:176px;height:48px;background:var(--blue);color:var(--white)}

/* ornament */
.wings{width:70px;height:40px;border-radius:20px;background:#c8bfb6}

/* intro */
.intro-title{top:828px;left:0;width:1200px;font-family:"Cinzel",serif;font-weight:700;font-size:32px;line-height:1.25;color:var(--brown)}
.intro-text{top:902px;left:320px;width:560px;font-size:18px;line-height:1.55;color:var(--grey);text-align:center}
.service{width:260px;height:232px;background:var(--white);border:1px solid var(--line);border-radius:6px;box-shadow:0 4px 14px rgba(0,0,0,.07);display:flex;flex-direction:column;align-items:center;padding-top:28px}
.service-icon{width:82px;height:82px;border-radius:50%;border:5px solid #e6e6e6;display:flex;align-items:center;justify-content:center;box-shadow:0 2px 6px rgba(0,0,0,.12)}
.service-label{margin-top:20px;font-family:"Cinzel",serif;font-size:15px;line-height:1.35;color:var(--grey);text-align:center;width:170px}

/* video */
.video{top:1365px;left:306px;width:578px;height:367px;background:var(--white);border:1px solid var(--line);box-shadow:0 4px 16px rgba(0,0,0,.08);padding:16px}
.video-still{width:100%;height:100%;background:linear-gradient(135deg,#d8d2cc 0%,#a39a92 45%,#5f5750 100%);position:relative}
.play{position:absolute;left:50%;top:50%;width:66px;height:66px;margin:-33px 0 0 -33px;border-radius:50%;background:#111;display:flex;align-items:center;justify-content:center}

/* events */
.section-title{font-family:"Cinzel",serif;font-weight:700;font-size:34px;letter-spacing:1px}
.calendar{top:1974px;left:161px;width:378px;height:365px;background:var(--white);border-radius:6px;padding:18px 22px}
.cal-head{height:44px;border-radius:22px;background:#b6a99d;display:flex;align-items:center;justify-content:space-between;padding:0 8px;color:var(--white);font-family:"Cinzel",serif;font-weight:700;font-size:19px}
.cal-nav{width:28px;height:28px;border-radius:50%;background:rgba(255,255,255,.35)}
.cal-grid{display:grid;grid-template-columns:repeat(7,1fr);margin-top:14px;row-gap:17px;text-align:center;font-size:16px;color:var(--ink)}
.cal-grid .dow{font-weight:700;font-size:15px}
.event{left:574px;width:460px;height:120px;display:flex;gap:16px}
.event-photo{width:112px;height:112px;border-radius:50%;flex:none}
.event-body{color:var(--white);padding-top:16px}
.event-title{font-size:19px;font-weight:400}
.event-text{font-size:12px;line-height:1.3;margin-top:5px;width:320px}
.event-more{font-size:12px;font-weight:700;margin-top:4px;letter-spacing:.3px}

/* board */
.member{width:200px;display:flex;flex-direction:column;align-items:center}
.member-photo{width:194px;height:194px;border-radius:50%;border:3px solid #d6d6d6}
.member-name{margin-top:26px;font-size:19px;color:var(--ink)}
.member-text{margin-top:6px;font-size:12px;line-height:1.3;color:var(--grey);text-align:center;width:160px}
.member-btn{margin-top:14px;width:134px;height:38px;border:1.5px solid #9b9b9b;border-radius:19px;display:flex;align-items:center;justify-content:center;font-size:12px;font-weight:700;color:var(--grey)}

/* testimonial */
.quote{top:3222px;left:240px;width:720px;color:var(--white);font-size:21px;font-weight:300;line-height:1.45;text-align:center}
.quote-mark{display:inline-block;font-family:"Cinzel",serif;font-size:44px;font-weight:700;line-height:20px;height:20px;vertical-align:-10px;margin:0 4px}
.quote-name{top:3340px;left:0;width:1200px;font-family:"Cinzel",serif;font-size:22px;color:var(--white);text-align:center;letter-spacing:1px}
.dots{top:3398px;left:0;width:1200px;display:flex;justify-content:center;gap:8px}
.dot{width:12px;height:12px;border-radius:50%;border:1.5px solid var(--white)}
.dot.on{background:var(--white)}

/* cta */
.cta{top:3587px;width:426px;height:284px;border-radius:0 60px 0 60px;color:var(--white);text-align:center;padding-top:50px}
.cta-title{font-family:"Cinzel",serif;font-weight:700;font-size:28px;letter-spacing:1px}
.cta-text{margin:12px auto 0;width:330px;font-size:14px;line-height:1.4}
.cta-btn{margin:18px auto 0;width:164px;height:46px;border:2px solid var(--white);border-radius:23px;display:flex;align-items:center;justify-content:center;font-size:13px;font-weight:700;letter-spacing:.5px}

/* contact */
.contact-bg{top:3942px;left:0;width:1200px;height:500px;background:linear-gradient(180deg,#f3eee9 0%,#e9e1d9 100%)}
.field{height:46px;background:var(--white);border:1px solid #e2ddd8;font-size:15px;color:var(--grey);padding:13px 16px}
.submit{top:4318px;left:516px;width:170px;height:46px;border-radius:23px;background:var(--blue-dark);color:var(--white);font-size:17px;font-weight:700;display:flex;align-items:center;justify-content:center}

/* footer */
.footer{top:4436px;left:0;width:1200px;height:340px;background:var(--blue)}
.footer-brand{top:4512px;left:168px;width:160px;height:160px;border-radius:50%;background:var(--white);display:flex;align-items:center;justify-content:center;padding:18px}
.foot-col{top:4510px}
.foot-head{font-family:"Cinzel",serif;font-weight:700;font-size:16px;color:var(--brown);margin-bottom:14px;letter-spacing:.5px}
.foot-line{display:flex;gap:10px;font-size:13px;line-height:1.4;color:var(--brown);margin-bottom:14px}
.foot-link{font-size:14px;line-height:1.55;color:var(--brown)}
.social{display:flex;gap:8px}
.social span{width:30px;height:30px;border-radius:50%;background:#4a6fb0}
.badge{margin:18px 0 0 18px;width:84px;height:84px;border-radius:50%;background:radial-gradient(circle,#f0d27a 0%,#c9a13c 70%,#a9842a 100%)}
.copyright{top:4775px;left:0;width:1200px;height:64px;background:var(--blue-dark);font-size:13px;color:var(--brown);display:flex;align-items:center;justify-content:center}
</style>
</head>
<body>

<!-- header -->
<header class="site-header abs">
  <nav class="nav nav-left abs"><span>ABOUT</span><span>HOW YOU CAN HELP</span><span>SERVICES</span></nav>
  <nav class="nav nav-right abs"><span>OUR LOVE OF PETS</span><span>CONTACT US</span><span>HAVEN WALK</span></nav>
</header>
<div class="brand abs"><div class="brand-name">Pine Hollow Haven Home Inc.</div></div>

<!-- hero -->
<section class="hero abs" role="img" aria-label="Photo of young women studying together on a living room floor">
  <div class="hero-arrow abs" style="left:84px"><svg width="14" height="18" viewBox="0 0 14 18"><path d="M10 2 3 9l7 7" fill="none" stroke="#444" stroke-width="2.5"/></svg></div>
  <div class="hero-arrow abs" style="left:1032px"><svg width="14" height="18" viewBox="0 0 14 18"><path d="M4 2l7 7-7 7" fill="none" stroke="#444" stroke-width="2.5"/></svg></div>
  <div class="hero-title abs"><div class="pre">WELCOME TO</div><div class="main">PINE HOLLOW HAVEN HOME INC</div></div>
  <div class="hero-buttons abs"><span class="btn btn-outline">OUR MISSION</span><span class="btn btn-blue">OUR GIRLS</span></div>
</section>
<svg class="abs" style="top:690px;left:0" width="1200" height="100" viewBox="0 0 1200 100" preserveAspectRatio="none">
  <path d="M0 70 Q600 -10 1200 40 L1200 100 L0 100Z" fill="#a9c0ce"/>
  <path d="M0 82 Q600 20 1200 62 L1200 100 L0 100Z" fill="#ffffff"/>
</svg>

<!-- intro -->
<div class="wings abs" role="img" aria-label="Small wings ornament" style="top:778px;left:565px"></div>
<h1 class="intro-title abs center">WE ARE PINE HOLLOW<br>HAVEN HOME</h1>
<p class="intro-text abs">With the help of our community, we have raised over 1000 girls and counting! Some of the services we offer include:</p>

<div class="service abs" style="top:1010px;left:180px">
  <div class="service-icon"><svg width="40" height="40" viewBox="0 0 40 40"><path d="M6 20 20 8l14 12M10 17v15h20V17" fill="none" stroke="#d8608a" stroke-width="3"/><rect x="17" y="23" width="6" height="9" fill="#d8608a"/></svg></div>
  <div class="service-label">ROOM, BOARD, AND WATCHFUL OVERSIGHT</div>
</div>
<div class="service abs" style="top:1048px;left:465px">
  <div class="service-icon"><svg width="40" height="40" viewBox="0 0 40 40"><path d="M20 33 7 20a7 7 0 0 1 13-9 7 7 0 0 1 13 9Z" fill="none" stroke="#d8608a" stroke-width="3"/></svg></div>
  <div class="service-label">TRANSITIONAL LIVING SERVICES</div>
</div>
<div class="service abs" style="top:1010px;left:752px">
  <div class="service-icon"><svg width="40" height="40" viewBox="0 0 40 40"><circle cx="20" cy="13" r="6" fill="none" stroke="#d8608a" stroke-width="3"/><path d="M9 34c0-7 5-12 11-12s11 5 11 12" fill="none" stroke="#d8608a" stroke-width="3"/></svg></div>
  <div class="service-label">INDEPENDENT LIVING SERVICES</div>
</div>

<!-- video -->
<div class="video abs"><div class="video-still" role="img" aria-label="Video still of a bright living room with a fireplace">
  <div class="play"><svg width="24" height="26" viewBox="0 0 24 26"><path d="M4 2l18 11L4 24Z" fill="#fff"/></svg></div>
</div></div>

<!-- events -->
<svg class="abs" style="top:1790px;left:0" width="1200" height="700" viewBox="0 0 1200 700" preserveAspectRatio="none">
  <path d="M0 70 Q600 -10 1200 30 L1200 90 L0 90Z" fill="#a9c0ce"/>
  <path d="M0 95 Q600 10 1200 45 L1200 660 Q600 700 0 630Z" fill="#9b8b7d"/>
  <path d="M0 630 Q600 700 1200 660 L1200 672 Q600 712 0 642Z" fill="#a9c0ce"/>
</svg>
<div class="wings abs" role="img" aria-label="Small wings ornament" style="top:1838px;left:565px;background:#e4ddd6"></div>
<h2 class="section-title abs center" style="top:1884px;left:0;width:1200px;color:#fff">EVENT CALENDAR</h2>

<div class="calendar abs">
  <div class="cal-head"><span class="cal-nav"></span><span>MARCH 2019</span><span class="cal-nav"></span></div>
  <div class="cal-grid">
    <span class="dow">MO</span><span class="dow">TU</span><span class="dow">WE</span><span class="dow">TH</span><span class="dow">FR</span><span class="dow">SA</span><span class="dow">SU</span>
    <span>1</span><span>2</span><span>3</span><span>4</span><span>5</span><span>6</span><span>7</span>
    <span>8</span><span>9</span><span>10</span><span>11</span><span>12</span><span>13</span><span>14</span>
    <span>15</span><span>16</span><span>17</span><span>18</span><span>19</span><span>20</span><span>21</span>
    <span>22</span><span>23</span><span>24</span><span>25</span><span>26</span><span>27</span><span>28</span>
    <span>29</span><span>30</span><span>31</span>
  </div>
</div>

<div class="event abs" style="top:1978px">
  <div class="event-photo" role="img" aria-label="Event photo of a stage with purple lights" style="background:linear-gradient(135deg,#7a3fa0,#2c1a45)"></div>
  <div class="event-body"><div class="event-title">Event Title here</div><div class="event-text">Lorem ipsum dolor sit amet consectetuer adipiscing elit Nam cursus Morbi ut mi Nullam enim leo</div><div class="event-more">READ MORE</div></div>
</div>
<div class="event abs" style="top:2111px">
  <div class="event-photo" role="img" aria-label="Event photo of friends gathered together" style="background:linear-gradient(135deg,#c7a98e,#6c5443)"></div>
  <div class="event-body"><div class="event-title">Event Title here</div><div class="event-text">Lorem ipsum dolor sit amet consectetuer adipiscing elit Nam cursus Morbi ut mi Nullam enim leo</div><div class="event-more">READ MORE</div></div>
</div>
<div class="event abs" style="top:2246px">
  <div class="event-photo" role="img" aria-label="Event photo of a smiling guest" style="background:linear-gradient(135deg,#d9c6b4,#4d3c31)"></div>
  <div class="event-body"><div class="event-title">Event Title here</div><div class="event-text">Lorem ipsum dolor sit amet consectetuer adipiscing elit Nam cursus Morbi ut mi Nullam enim leo</div><div class="event-more">READ MORE</div></div>
</div>

<!-- board -->
<div class="wings abs" role="img" aria-label="Small wings ornament" style="top:2502px;left:565px"></div>
<h2 class="section-title abs center" style="top:2548px;left:0;width:1200px;color:var(--brown)">BOARD MEMBERS</h2>
<div class="member abs" style="top:2620px;left:165px"><div class="member-photo" role="img" aria-label="Portrait of a board member" style="background:linear-gradient(160deg,#e6d3c3,#8a6d58)"></div><div class="member-name">Member Name</div><div class="member-text">Class aptent taciti sociosqu ad litora torquent</div><div class="member-btn">READ MORE</div></div>
<div class="member abs" style="top:2620px;left:384px"><div class="member-photo" role="img" aria-label="Portrait of a board member" style="background:linear-gradient(160deg,#d7d2cc,#8d8680)"></div><div class="member-name">Member Name</div><div class="member-text">Class aptent taciti sociosqu ad litora torquent</div><div class="member-btn">READ MORE</div></div>
<div class="member abs" style="top:2620px;left:603px"><div class="member-photo" role="img" aria-label="Portrait of a board member" style="background:linear-gradient(160deg,#f0f0f0,#6f7f98)"></div><div class="member-name">Member Name</div><div class="member-text">Class aptent taciti sociosqu ad litora torquent</div><div class="member-btn">READ MORE</div></div>
<div class="member abs" style="top:2620px;left:835px"><div class="member-photo" role="img" aria-label="Portrait of a board member" style="background:linear-gradient(160deg,#eeeae6,#a48b76)"></div><div class="member-name">Member Name</div><div class="member-text">Class aptent taciti sociosqu ad litora torquent</div><div class="member-btn">READ MORE</div></div>

<!-- testimonial -->
<svg class="abs" style="top:3020px;left:0" width="1200" height="520" viewBox="0 0 1200 520" preserveAspectRatio="none" role="img" aria-label="Dark warm photo backdrop of hands writing">
  <defs><linearGradient id="testimonialShade" x1="0" y1="0" x2="1" y2="1"><stop offset="0" stop-color="#5a4a3f"/><stop offset=".5" stop-color="#3d322b"/><stop offset="1" stop-color="#6b5a4c"/></linearGradient></defs>
  <path d="M0 10 L1200 40 L1200 480 Q600 450 0 500Z" fill="url(#testimonialShade)"/>
  <path d="M0 0 Q500 30 1200 0 L1200 50 Q600 20 0 14Z" fill="#a9c0ce"/>
  <path d="M0 500 Q600 440 1200 480 L1200 520 L0 520Z" fill="#a9c0ce"/>
  <path d="M0 512 Q600 460 1200 500 L1200 520 L0 520Z" fill="#ffffff"/>
</svg>
<div class="wings abs" role="img" aria-label="Small wings ornament" style="top:3100px;left:565px;background:#e4ddd6"></div>
<h2 class="section-title abs center" style="top:3146px;left:0;width:1200px;color:#fff">WHAT OUR GIRLS SAY</h2>
<p class="quote abs"><span class="quote-mark">“</span>Emotionally heled a lot and I felt supported.  I learned how to cook, budget, get a job, buy a car, pay bills, community service and helpping others.  I would not have gotten here without the Haven Home.<span class="quote-mark">”</span></p>
<div class="quote-name abs">MADELINE</div>
<div class="dots abs"><span class="dot"></span><span class="dot on"></span><span class="dot"></span></div>

<!-- cta -->
<div class="cta abs" role="img" aria-label="Donate panel with a warm photo backdrop" style="left:168px;background:linear-gradient(135deg,#8d7867,#75604f)">
  <div class="cta-title">DONATE</div>
  <p class="cta-text">We appreciate donations from our community! It is because of the hearts of those around us that we're able to do what we do.</p>
  <div class="cta-btn">DONATE NOW</div>
</div>
<div class="cta abs" role="img" aria-label="Accreditation panel with a soft blue photo backdrop" style="left:619px;background:linear-gradient(135deg,#a9c0ce,#b9ccd7)">
  <div class="cta-title">CRCS</div>
  <p class="cta-text">Council for Residential Care Standards. Facilities certified since 2009. To learn more about our CRCS International accreditation, please visit www.crcs-example.org</p>
  <div class="cta-btn">CLICK HERE</div>
</div>

<!-- contact -->
<div class="contact-bg abs" role="img" aria-label="Faded photo backdrop of a young woman"></div>
<svg class="abs" style="top:3930px;left:0" width="1200" height="520" viewBox="0 0 1200 520" preserveAspectRatio="none">
  <path d="M0 70 Q500 -10 1200 20 L1200 0 L0 0Z" fill="#ffffff"/>
  <path d="M0 70 Q500 -10 1200 20 L1200 34 Q500 4 0 84Z" fill="#4b3f36"/>
  <path d="M0 440 Q700 480 1200 400 L1200 520 L0 520Z" fill="#4b3f36"/>
  <path d="M0 456 Q700 496 1200 418 L1200 520 L0 520Z" fill="#a9c0ce"/>
</svg>
<div class="wings abs" role="img" aria-label="Small wings ornament" style="top:3980px;left:565px"></div>
<h2 class="section-title abs center" style="top:4024px;left:0;width:1200px;color:var(--brown)">CONTACT US</h2>
<div class="field abs" style="top:4084px;left:194px;width:402px">Your Name</div>
<div class="field abs" style="top:4084px;left:612px;width:407px">Phone</div>
<div class="field abs" style="top:4142px;left:194px;width:402px">Email</div>
<div class="field abs" style="top:4142px;left:612px;width:407px">City</div>
<div class="field abs" style="top:4203px;left:194px;width:825px;height:88px">Message</div>
<div class="submit abs">Submit</div>

<!-- footer -->
<footer>
<div class="footer abs"></div>
<div class="footer-brand abs"><div class="brand-name" style="font-size:17px">Pine Hollow Haven Home Inc.</div></div>
<div class="foot-col abs" style="left:447px;width:230px">
  <div class="foot-head">CONTACT US</div>
  <div class="foot-line"><svg width="14" height="18" viewBox="0 0 14 18"><path d="M7 17S1 10 1 6.5a6 6 0 0 1 12 0C13 10 7 17 7 17Z" fill="#4b3f36"/><circle cx="7" cy="6.5" r="2.2" fill="#a9c0ce"/></svg><span>418 Birchwood Ln, Alder Falls,<br>ST 00000, USA</span></div>
  <div class="foot-line"><svg width="14" height="16" viewBox="0 0 14 16"><path d="M3 1h3l1 4-2 1.5a8 8 0 0 0 3.5 3.5L10 8l4 1v3c0 1-1 2-2 2A11 11 0 0 1 1 3c0-1 1-2 2-2Z" fill="#4b3f36"/></svg><span>555.010.2471</span></div>
  <div class="foot-line"><svg width="16" height="14" viewBox="0 0 16 14"><rect x="1" y="2" width="14" height="10" fill="none" stroke="#4b3f36" stroke-width="1.6"/><path d="M1 2l7 6 7-6" fill="none" stroke="#4b3f36" stroke-width="1.6"/></svg><span>hello@pinehollowhaven.org</span></div>
</div>
<div class="foot-col abs" style="left:716px;width:160px">
  <div class="foot-head">COMPANY</div>
  <div class="foot-link">About us</div><div class="foot-link">Haven Walk</div><div class="foot-link">Services</div><div class="foot-link">How you can help</div><div class="foot-link">Our Love of Pets</div>
</div>
<div class="foot-col abs" style="left:905px;width:160px">
  <div class="foot-head">GET IN TOUCH</div>
  <div class="social"><span></span><span style="background:#3f9fd8"></span><span style="background:#4a6fb0"></span><span style="background:#2f6fa8"></span></div>
  <div class="badge" role="img" aria-label="Award badge"></div>
</div>
<div class="copyright abs">Copyright © 2019 All right reserved</div>
</footer>

</body>
</html>
```